Harborview Optical -Window Poster (Optometrist)

We are an optometry practice and we need a poster for a new store promotion for our window highlighting we now also sell 2 pairs of glasses as a package deal. The size will be 1300mm width x 1900mm height

The artwork will be displayed as a fabric banner in our shop window. We have 7 other banners with different services our business provides. The words needs to standout for passers by and the cars stopped at the traffic lights out front of our business. We already have signs with our logos phone number etc. so we won't need them included in the poster.

It would need to include the following information.

Two pair packages now available*

*Conditions apply

The artwork will be displayed as a fabric banner in our shop window. We have 7 other banners with different services our business provides. The words needs to standout for passers by and the cars stopped at the traffic lights out front of our business. We already have signs with our logos phone number etc. so we won't need them included in the poster. Thank you for your work it's amazing Added Saturday, February 18, 2017

The artwork will be displayed as a fabric banner in our shop window. We have 7 other banners with different services our business provides. The words needs to standout for passers by and the cars stopped at the traffic lights out front of our business. We already have signs with our logos phone number etc. so we won't need them included in the poster. Added Saturday, February 18, 2017

Target Market(s)

Cars driving past and stopped at traffic lights outside our store.

Industry/Entity Type

Optician

Requirements
Must have
• Poster must say:
• Two pair packages now available*
• *Conditions apply

```html
<!DOCTYPE html>
<html lang="en">
<head>
<meta charset="utf-8">
<title>Harborview Optical – Two Pair Packages Window Poster</title>
<link rel="stylesheet" href="https://fonts.googleapis.com/css2?family=Archivo+Black&family=Roboto+Condensed:wght@400;800&family=Oswald:wght@600&display=swap">
<style>
  :root {
    --plum-deep: #1f0510;
    --plum: #6a1238;
    --plum-bright: #8e1f55;
    --panel: #f2f3f5;
    --ink: #060606;
    --red: #e8202a;
    --yellow: #ffd400;
    --yellow-bright: #ffec00;
    --line: #ffffff;
  }
  * { margin: 0; padding: 0; box-sizing: border-box; }
  html, body { width: 962px; height: 1200px; overflow: hidden; background: var(--plum-deep); }
  .poster {
    position: relative;
    width: 962px;
    height: 1200px;
    overflow: hidden;
    background:
      radial-gradient(ellipse 160px 40px at 50% 0%, rgba(255,170,180,.85), transparent 100%),
      radial-gradient(ellipse 170px 45px at 50% 100%, rgba(255,170,180,.85), transparent 100%),
      radial-gradient(ellipse 70% 55% at 55% 55%, var(--plum-bright), var(--plum) 55%, var(--plum-deep) 100%);
  }
  .poster__texture {
    position: absolute; inset: 0;
    background: radial-gradient(ellipse 40% 25% at 75% 85%, rgba(190,60,120,.35), transparent 70%),
                radial-gradient(ellipse 35% 25% at 10% 70%, rgba(160,40,100,.3), transparent 70%);
  }
  .headline-frame { position: absolute; left: 63px; top: 64px; width: 855px; height: 104px; }
  .headline {
    position: absolute; left: 63px; top: 64px; width: 855px; height: 104px;
    display: flex; align-items: center; justify-content: center;
    font-family: "Roboto Condensed", sans-serif; font-weight: 400;
    font-size: 106px; line-height: 1; color: var(--yellow); letter-spacing: 1px;
    padding-top: 4px;
  }
  .offer-outline { position: absolute; left: 0; top: 0; width: 962px; height: 1200px; }
  .offer-panel {
    position: absolute; left: 83px; top: 225px; width: 800px; height: 599px;
    background: var(--panel);
  }
  .offer-title {
    position: absolute; left: 83px; top: 318px; width: 800px; text-align: center;
    font-family: "Roboto Condensed", sans-serif; font-weight: 800;
    font-size: 188px; line-height: 1; color: var(--ink); letter-spacing: 2px;
    white-space: nowrap;
  }
  .offer-subtitle {
    position: absolute; left: 83px; top: 532px; width: 800px; text-align: center;
    font-family: "Archivo Black", sans-serif; font-weight: 400;
    font-size: 118px; line-height: 1; color: var(--red); letter-spacing: 0;
    text-shadow: 4px 5px 0 var(--ink);
    white-space: nowrap;
  }
  .terms-frame { position: absolute; left: 254px; top: 971px; width: 456px; height: 104px; }
  .terms {
    position: absolute; left: 254px; top: 971px; width: 456px; height: 104px;
    display: flex; align-items: center; justify-content: center;
    font-family: "Oswald", sans-serif; font-weight: 600;
    font-size: 48px; line-height: 1; color: var(--yellow-bright); letter-spacing: 2px;
    white-space: nowrap;
  }
</style>
</head>
<body>
  <main class="poster">
    <div class="poster__texture" role="img" aria-label="Faint textured backdrop of eyeglasses and printed text in deep magenta"></div>

    <svg class="headline-frame" viewBox="0 0 855 104" aria-hidden="true">
      <polyline points="272,102 2,102 2,2 853,2 853,102 644,102" fill="none" stroke="var(--line)" stroke-width="3"/>
    </svg>
    <p class="headline">NOW AVAILABLE*</p>

    <svg class="offer-outline" viewBox="0 0 962 1200" aria-hidden="true">
      <polygon points="53,256 849,196 914,794 118,851" fill="none" stroke="var(--line)" stroke-width="3"/>
    </svg>
    <div class="offer-panel"></div>
    <h1 class="offer-title">TWO PAIR</h1>
    <h2 class="offer-subtitle">PACKAGES</h2>

    <svg class="terms-frame" viewBox="0 0 456 104" aria-hidden="true">
      <polyline points="120,2 2,2 2,102 454,102 454,2 335,2" fill="none" stroke="var(--line)" stroke-width="3"/>
    </svg>
    <p class="terms">*CONDITIONS APPLY</p>
  </main>
</body>
</html>
```